Quorva - corporate Business Card

We need a good look and innovative business card for a new start up company based in Los Angeles called "Quorva". We are in a payment business, including payment card, app, and ewallet. We are expert in online payment and Card not present (CNP) transaction.
We need an innovative, modern business card.

Our logo font is Aero Matics

Target Market(s)

Startup - Bank - Online Payment - Card Manufacturing

Industry/Entity Type

Startup

Contact Information for Business Card

phone: 555 014 7396 - Address: 4172 Marlowe blvd, Corvell Bay, QR 90299

Requirements
Must have
• Message: innovative, professional, expert, high tech, trust, online payment expert, security
Nice to have
• no comment
Should not have
• no Comment

```html
<!DOCTYPE html>
<html lang="en">
<head>
<meta charset="utf-8">
<title>Quorva – Business Card</title>
<link rel="stylesheet" href="https://fonts.googleapis.com/css2?family=Open+Sans:wght@400;600;700&display=swap">
<style>
  :root {
    --page-bg: #d9d6d2;
    --card-bg: #f3f2f0;
    --brand-red: #9b1b26;
    --ink: #2b2b2b;
  }
  * { margin: 0; padding: 0; box-sizing: border-box; }
  html, body {
    width: 1200px;
    height: 969px;
    overflow: hidden;
    background: var(--page-bg);
    font-family: "Open Sans", Arial, sans-serif;
  }
  .card {
    position: absolute;
    left: 100px;
    top: 201px;
    width: 1000px;
    height: 566px;
    background: var(--card-bg);
    border-radius: 26px;
    box-shadow: 0 10px 30px rgba(0,0,0,0.15);
    overflow: hidden;
  }
  .brand-disc {
    position: absolute;
    left: 26px;
    top: 26px;
    width: 514px;
    height: 514px;
    border-radius: 50%;
    background: var(--brand-red);
  }
  .edge-tab {
    position: absolute;
    right: -24px;
    top: 76px;
    width: 52px;
    height: 66px;
    border-radius: 50%;
    background: var(--brand-red);
  }
  .contact {
    position: absolute;
    right: 62px;
    top: 70px;
    text-align: right;
    color: var(--ink);
  }
  .contact-name {
    font-size: 31px;
    font-weight: 700;
    color: var(--brand-red);
    line-height: 38px;
  }
  .contact-role {
    font-size: 24px;
    line-height: 34px;
  }
  .contact-address {
    margin-top: 38px;
    font-size: 23px;
    line-height: 34px;
  }
  .contact-lines {
    margin-top: 16px;
    list-style: none;
    font-size: 23px;
    line-height: 40px;
  }
  .contact-lines li {
    display: flex;
    justify-content: flex-end;
    align-items: center;
    gap: 12px;
  }
  .contact-lines svg { width: 22px; height: 22px; fill: var(--brand-red); }
  .wordmark {
    position: absolute;
    right: 62px;
    top: 400px;
    font-size: 82px;
    font-weight: 600;
    color: var(--brand-red);
    letter-spacing: 1px;
    line-height: 1;
  }
</style>
</head>
<body>
  <div class="card">
    <div class="brand-disc"></div>
    <div class="edge-tab"></div>

    <div class="contact">
      <p class="contact-name">DANA REYES</p>
      <p class="contact-role">CEO&amp;Founder</p>
      <p class="contact-address">4172 Marlowe blvd<br>Corvell Bay, QR 90299</p>
      <ul class="contact-lines">
        <li>555 014 7396
          <svg viewBox="0 0 24 24" aria-hidden="true"><path d="M6.6 10.8a15.1 15.1 0 0 0 6.6 6.6l2.2-2.2a1 1 0 0 1 1-.25 11.4 11.4 0 0 0 3.6.57 1 1 0 0 1 1 1V20a1 1 0 0 1-1 1A17 17 0 0 1 3 4a1 1 0 0 1 1-1h3.5a1 1 0 0 1 1 1c0 1.25.2 2.45.57 3.57a1 1 0 0 1-.25 1z"/></svg>
        </li>
        <li>dana@quorva.com
          <svg viewBox="0 0 24 24" aria-hidden="true"><path d="M2 5h20v14H2z"/><path d="M3.5 6.5 12 12.5l8.5-6" fill="none" stroke="#f3f2f0" stroke-width="1.6"/></svg>
        </li>
        <li>www.quorva.com
          <svg viewBox="0 0 24 24" aria-hidden="true"><circle cx="12" cy="12" r="10"/><path d="M12 2v20M2 12h20M12 2c-4 4-4 16 0 20M12 2c4 4 4 16 0 20" fill="none" stroke="#f3f2f0" stroke-width="1.3"/></svg>
        </li>
      </ul>
    </div>

    <p class="wordmark">quorva</p>
  </div>
</body>
</html>
```